Automotive Accessories Business Card

Design a business template that match our new logo design and our industry.

https://www.qelmotorgear.com/

Target Market(s)

Aftermarket auto parts and accessories

Industry/Entity Type

automotive

Contact Information for Business Card

company logo

Font styles to use
Serif
Sans Serif

Colors
EB3D1F
EC4F4E
F09395
F8D3D4
FCEDEE

```html
<!DOCTYPE html>
<html lang="en">
<head>
<meta charset="utf-8">
<title>QEL Motor Gear – Business Card</title>
<link href="https://fonts.googleapis.com/css2?family=Montserrat:wght@400;500;700&display=swap" rel="stylesheet">
<style>
  :root {
    --backdrop: #e9e9ea;
    --card: #3e3e40;
    --card-deep: #2a2a2c;
    --red: #d92128;
    --white: #ffffff;
    --soft: #d9d9db;
    --rule: #bdbdbf;
  }
  * { box-sizing: border-box; margin: 0; padding: 0; }
  html, body { width: 1200px; height: 802px; overflow: hidden; }
  body {
    background: var(--backdrop);
    font-family: "Montserrat", Arial, sans-serif;
    position: relative;
  }
  .card {
    position: absolute;
    top: 246px;
    width: 520px;
    height: 310px;
    background: var(--card);
    border-bottom: 4px solid var(--red);
    overflow: hidden;
  }
  .card--front { left: 50px; }
  .card--back { left: 630px; }

  /* front */
  .brand {
    position: absolute;
    top: 54px;
    left: 0;
    right: 0;
    text-align: center;
    color: var(--white);
    font-weight: 700;
    font-size: 26px;
    letter-spacing: 3px;
    display: flex;
    align-items: center;
    justify-content: center;
    gap: 12px;
  }
  .brand__square { width: 16px; height: 16px; background: var(--red); }
  .divider {
    position: absolute;
    top: 150px;
    left: 36px;
    right: 36px;
    height: 1px;
    background: var(--rule);
  }
  .address {
    position: absolute;
    top: 84px;
    right: 36px;
    text-align: right;
    color: var(--soft);
    font-size: 13px;
    line-height: 1.45;
    display: none;
  }
  .person {
    position: absolute;
    left: 36px;
    top: 172px;
  }
  .person__name {
    color: var(--red);
    font-weight: 700;
    font-size: 18px;
    letter-spacing: 2.5px;
    text-transform: uppercase;
  }
  .person__role { color: var(--soft); font-size: 13px; margin-top: 2px; }
  .person__rule { width: 200px; height: 1px; background: var(--rule); margin: 10px 0 8px; }
  .contacts { list-style: none; }
  .contacts li {
    color: var(--soft);
    font-size: 13px;
    line-height: 21px;
    display: flex;
    align-items: center;
    gap: 8px;
  }
  .contacts svg { width: 11px; height: 11px; flex: none; }
  .location {
    position: absolute;
    right: 36px;
    top: 172px;
    text-align: right;
    color: var(--soft);
    font-size: 13px;
    line-height: 1.5;
  }

  /* back */
  .pattern {
    position: absolute;
    inset: 0;
    background: linear-gradient(120deg, var(--card-deep) 0%, #333335 45%, #6d6d70 100%);
  }
  .back-brand {
    position: absolute;
    left: 0; right: 0;
    top: 138px;
    text-align: center;
    color: var(--white);
    font-weight: 700;
    font-size: 20px;
    letter-spacing: 2px;
    display: flex;
    align-items: center;
    justify-content: center;
    gap: 10px;
  }
  .back-brand .brand__square { width: 13px; height: 13px; }
</style>
</head>
<body>

<section class="card card--front">
  <div class="brand"><span class="brand__square"></span>QEL MOTOR GEAR INC</div>
  <div class="divider"></div>

  <div class="person">
    <p class="person__name">Daniel Reyes</p>
    <p class="person__role">Manager</p>
    <div class="person__rule"></div>
    <ul class="contacts">
      <li>
        <svg viewBox="0 0 12 12"><path fill="var(--red)" d="M2.5 1 L4.5 1 L5.2 3.6 L4 4.6 Q5 7 7.4 8 L8.4 6.8 L11 7.5 L11 9.5 Q11 11 9.5 11 Q1 10 1 2.5 Q1 1 2.5 1Z"/></svg>
        1-866-555-0148
      </li>
      <li>
        <svg viewBox="0 0 12 12"><rect x="0.5" y="2" width="11" height="8" fill="var(--red)"/><path d="M0.5 2 L6 6.5 L11.5 2" stroke="var(--card)" stroke-width="1.2" fill="none"/></svg>
        sales@qelmotorgear.com
      </li>
      <li>
        <svg viewBox="0 0 12 12"><circle cx="6" cy="6" r="5.5" fill="var(--red)"/><path d="M0.5 6 H11.5 M6 0.5 Q2.5 6 6 11.5 M6 0.5 Q9.5 6 6 11.5" stroke="var(--card)" stroke-width="0.9" fill="none"/></svg>
        www.qelmotorgear.com
      </li>
    </ul>
  </div>

  <address class="location">
    240 W. Elm Ave.<br>
    Unit B<br>
    Fontana, CA 92335
  </address>
</section>

<section class="card card--back">
  <div class="pattern" role="img" aria-label="Repeating embossed brand pattern in dark and light grey"></div>
  <div class="back-brand"><span class="brand__square"></span>QEL MOTOR GEAR INC</div>
</section>

</body>
</html>
```